RW Holloway LLC Business Card - Civil Engineering & Consulting Firm

We need a Business Card that is elegant, and masculine.  It is our Professional Civil Engineering & Consulting Company located in San Antonio TX (Not s construction or builder firm- no gears & no tool images please). We provide civil engineering services including  commercial site plans, grading and drainage plans, utility plans, hydraulics and hydrology, land planning, utility coordination, and other general civil engineering services related to commercial and residential development.
We have 2 existing Logos. We would like to convey reliability, strength, trustworthiness and attention to detail.  Blues and orange tones as per logo We are OK with the use of a darker blue in the mix.  We have 2 logo versions - Full Company Name Logo to go on the back of card, & Small Icon Logo for the front w/ personal Info.

Target Market(s)
Architects, Real Estate Developers, Other Strctural Engineers, Surveyers, General Contractors
Industry/Entity Type
Professional Civil Engineering
Contact Information for Business Card
Name, Position, Address, Cell & Office #, email, and company website
Font styles to use
Other font styles liked:
- Avian
Requirements
Should not have
- No Tools, No Gears, no Cranes, or Construction Equipment.

```html
<!DOCTYPE html>
<html lang="en">
<head>
<meta charset="UTF-8">
<title>RW Holloway LLC – Business Card</title>
<link href="https://fonts.googleapis.com/css2?family=Josefin+Sans:wght@300;400&family=Arimo:wght@400&display=swap" rel="stylesheet">
<style>
  :root {
    --page-bg: #c9c9c9;
    --card-bg: #2d2d2d;
    --edge-orange: #f0901e;
    --accent-orange: #f2922a;
    --accent-blue: #5fa3dc;
    --text-light: #e6e6e6;
    --emboss: #4a4a4a;
  }
  * { margin: 0; padding: 0; box-sizing: border-box; }
  html, body { width: 1200px; height: 800px; overflow: hidden; }
  body {
    background: var(--page-bg);
    display: flex;
    align-items: center;
    justify-content: center;
    gap: 48px;
  }
  .card {
    position: relative;
    width: 525px;
    height: 300px;
    background: var(--card-bg);
    border-bottom: 3px solid var(--edge-orange);
    overflow: hidden;
  }

  /* Front */
  .brand {
    position: absolute;
    top: 52px;
    right: 48px;
    display: flex;
    align-items: center;
    gap: 12px;
  }
  .brand-square {
    width: 18px; height: 18px;
    background: var(--accent-orange);
  }
  .brand-name {
    font-family: "Josefin Sans", sans-serif;
    font-weight: 300;
    font-size: 30px;
    letter-spacing: 3px;
    color: var(--accent-blue);
    text-transform: uppercase;
    white-space: nowrap;
  }
  .divider {
    position: absolute;
    left: 36px; right: 36px;
    top: 168px;
    height: 1px;
    background: var(--accent-blue);
  }
  .person {
    position: absolute;
    left: 36px;
    top: 112px;
  }
  .person-name {
    font-family: "Josefin Sans", sans-serif;
    font-weight: 400;
    font-size: 22px;
    letter-spacing: 1px;
    text-transform: uppercase;
  }
  .person-name .first { color: var(--accent-blue); }
  .person-name .last { color: var(--accent-orange); }
  .person-title {
    font-family: "Arimo", sans-serif;
    font-size: 14px;
    color: var(--text-light);
    margin-top: 4px;
  }
  .contact-list {
    position: absolute;
    left: 36px;
    top: 186px;
    list-style: none;
    font-family: "Arimo", sans-serif;
    font-size: 14px;
    color: var(--text-light);
  }
  .contact-list li {
    display: flex;
    align-items: center;
    gap: 8px;
    height: 24px;
  }
  .contact-list svg { width: 14px; height: 14px; color: var(--accent-blue); flex: none; }
  .contact-list .web-name { color: var(--accent-orange); }
  .address {
    position: absolute;
    right: 40px;
    top: 200px;
    text-align: right;
    font-family: "Arimo", sans-serif;
    font-style: normal;
    font-size: 14px;
    line-height: 1.5;
    color: var(--text-light);
  }

  /* Back */
  .card-back {
    display: flex;
    align-items: center;
    justify-content: center;
  }
  .back-brand {
    display: flex;
    align-items: center;
    gap: 16px;
  }
  .back-brand .brand-square { width: 26px; height: 26px; background: var(--emboss); }
  .back-brand .brand-name {
    font-size: 38px;
    color: var(--emboss);
  }
</style>
</head>
<body>

  <section class="card card-front">
    <div class="brand">
      <span class="brand-square"></span>
      <span class="brand-name">RW Holloway LLC</span>
    </div>

    <div class="person">
      <p class="person-name"><span class="first">Marcus</span> <span class="last">Delgado</span></p>
      <p class="person-title">Managing Director</p>
    </div>

    <div class="divider"></div>

    <ul class="contact-list">
      <li>
        <svg viewBox="0 0 24 24"><path fill="currentColor" d="M6.6 10.8a15.1 15.1 0 0 0 6.6 6.6l2.2-2.2a1 1 0 0 1 1-.25 11.4 11.4 0 0 0 3.6.57 1 1 0 0 1 1 1V20a1 1 0 0 1-1 1A17 17 0 0 1 3 4a1 1 0 0 1 1-1h3.5a1 1 0 0 1 1 1c0 1.25.2 2.45.57 3.57a1 1 0 0 1-.25 1z"/></svg>
        210-555-0147
      </li>
      <li>
        <svg viewBox="0 0 24 24"><path d="M2 5h20v14H2z M2 5l10 8 10-8" fill="none" stroke="currentColor" stroke-width="2"/></svg>
        info@hollowayeng.com
      </li>
      <li>
        <svg viewBox="0 0 24 24"><circle cx="12" cy="12" r="9" fill="none" stroke="currentColor" stroke-width="2"/><path d="M3 12h18M12 3c3 3 3 15 0 18M12 3c-3 3-3 15 0 18" fill="none" stroke="currentColor" stroke-width="1.6"/></svg>
        <span>www.<span class="web-name">hollowayeng</span>.com</span>
      </li>
    </ul>

    <address class="address">
      1180 Alamo Ridge Drive<br>
      San Antonio TX 78205
    </address>
  </section>

  <section class="card card-back">
    <div class="back-brand">
      <span class="brand-square"></span>
      <span class="brand-name">RW Holloway LLC</span>
    </div>
  </section>

</body>
</html>
```